CalmPeak Nurses' Manifesto

Design a manifesto to inspire and motivate nurses to work at minimum standards of excellence in their nursing practice.

The manifesto will become a feature of our website, at conferences, workshops and retreats. It will also be featured on other marketing tools.

Primary Market:
Nurses and/or other healthcare professionals (specifically Doctors, Occupational Therapists, Psychologists and Social Workers).

However the manifesto is equally applicable to all nurses and healthcare professionals from new graduates to very experienced senior clinicians, administration officers,managers and healthcare executive personnel.

Mainly females and primarily 35 to 65 years old, which suggests people in this target age group have extensive experience, but have become jaded'.

The purpose of our business is to assist healthcare professionals, primarily nurses, to maintain their enthusiasm and excellence in service provision, for their benefit as well as the benefit of the clients.

I have attached:
File 1: Copy Samples and examples: which has the copy for the manifesto, examples that appeal to us and our 3 attempts.
File 2: Our colour Spec Sheet, HOWEVER the colours are not necessary limited to these colours. These colours are not in the logo that will be on the manifesto. The colours on the logo attached can/or also be used.
File 3: Prototype logo. The final logo will be available within 3 to 4 days.

Industry/Entity Type

Healthcare

Requirements
Must have
• Must use the copy as per the attached file.

It should be contemporary, eye catching and motivational.

Should not have
• MUST BE EASY TO READ. Each line MUST be clearly defined from each other.

```html
<!DOCTYPE html>
<html lang="en">
<head>
<meta charset="utf-8">
<title>CalmPeak Nurses' Manifesto</title>
<link href="https://fonts.googleapis.com/css2?family=Questrial&display=swap" rel="stylesheet">
<style>
:root{
  --blue:#3b8fdc;--sky:#43a6e6;--pale-cyan:#92d8ef;--cyan:#4cc2ea;
  --yellow:#d8c51c;--green:#8cc63f;--mint:#6fd8c2;
  --ink:#1b1b1b;--grey:#7d7d7d;--light-grey:#c4c4c4;
  --magenta:#e6178b;--pink:#f28ccb;--red:#e8221f;--dark-red:#8e1b1b;--maroon:#5f1616;
  --lavender:#b48fe3;--purple:#9a4cd8;--navy:#1f4ea8;--orange:#f07a1b;
  --brown:#6b4a1d;--tan:#b58444;--band:#3f95e2;--photo-a:#a9dcd9;--photo-b:#e9dccb;
}
*{margin:0;padding:0;box-sizing:border-box}
html,body{width:900px;height:1200px;overflow:hidden;background:#fff}
.manifesto{position:relative;width:900px;height:1200px;font-family:"Questrial",sans-serif;color:var(--ink)}
.line{position:absolute;white-space:nowrap;line-height:1}
.spread{display:flex;justify-content:space-between}
.vertical{position:absolute;transform-origin:left top;transform:rotate(-90deg);white-space:nowrap;line-height:1}
.top-band{position:absolute;left:35px;top:0;width:840px;height:14px;background:var(--band)}
.foot-band{position:absolute;left:485px;top:1140px;width:390px;height:42px;background:var(--band);color:#fff;font-size:27px;padding:7px 0 0 28px}
.foot-band b{font-weight:400;font-size:34px;color:#eaf6ff}
.photo{position:absolute;left:640px;top:820px;width:240px;height:362px;background:linear-gradient(180deg,var(--photo-b),var(--photo-a) 55%,#8fcfd0)}
.brand{position:absolute;left:58px;top:1143px;display:flex;align-items:center;gap:10px;font-size:24px;color:#2d8a4a}
.brand i{display:block;width:40px;height:40px;background:#2d8a4a;border-radius:50%}
</style>
</head>
<body>
<main class="manifesto">
  <div class="top-band"></div>

  <div class="line" style="left:33px;top:22px;font-size:74px;color:var(--blue)">Nurse</div>
  <div class="line" style="left:237px;top:42px;font-size:26px;color:var(--yellow)">Deliver</div>
  <div class="line" style="left:377px;top:20px;font-size:52px;color:var(--blue)">care</div>
  <div class="line" style="left:484px;top:42px;font-size:28px;color:var(--yellow)">skillfully.</div>
  <div class="line" style="left:35px;top:95px;font-size:37px;color:var(--mint)">with open</div>
  <div class="line" style="left:240px;top:80px;font-size:52px;color:var(--green)">Learn</div>
  <div class="line spread" style="left:403px;top:80px;width:203px;font-size:25px;color:var(--green)"><span>s</span><span>o</span><span>m</span><span>e</span><span>t</span><span>h</span><span>i</span><span>n</span><span>g</span></div>
  <div class="line" style="left:403px;top:106px;font-size:25px;color:var(--green)">new each day.</div>
  <div class="line" style="left:35px;top:134px;font-size:39px;color:var(--mint)">hands, hearts and minds.</div>

  <div class="line" style="left:624px;top:14px;font-size:92px;color:var(--blue)">Trust</div>
  <div class="line" style="left:625px;top:114px;font-size:21px">your knowledge and</div>
  <div class="line" style="left:625px;top:136px;font-size:21px">seek <span style="color:var(--sky)">advice</span> only from</div>
  <div class="line" style="left:625px;top:154px;font-size:21px">respected <span style="color:var(--sky);font-size:27px">sources</span>.</div>

  <div class="line" style="left:35px;top:186px;font-size:27px">Look after</div>
  <div class="line" style="left:222px;top:168px;font-size:46px;color:var(--magenta)">yourself</div>
  <div class="line" style="left:35px;top:224px;font-size:27px">and value your <span style="color:var(--sky);font-size:37px">health</span></div>
  <div class="line spread" style="left:35px;top:259px;width:348px;font-size:27px"><span>as</span><span>much</span><span>as</span><span>you</span><span>value</span></div>
  <div class="line spread" style="left:35px;top:293px;width:348px;font-size:27px"><span>the</span><span style="color:var(--sky)">health</span><span>of</span><span>others.</span></div>
  <div class="line spread" style="left:35px;top:326px;width:348px;font-size:29px;color:var(--pale-cyan);align-items:flex-end"><span style="color:var(--sky);font-size:44px">Be</span><span>a</span><span>lifelong</span><span>learner.</span></div>
  <div class="line" style="left:33px;top:370px;font-size:56px;color:var(--red)">Respect</div>
  <div class="line" style="left:252px;top:398px;font-size:21px;color:#6d6d6d">the limits of</div>
  <div class="line" style="left:35px;top:430px;font-size:21px;color:#6d6d6d"><span style="color:var(--lavender);font-size:27px">people</span>'s knowledge and share</div>
  <div class="line spread" style="left:35px;top:459px;width:340px;font-size:21px;color:#6d6d6d"><span>your</span><span>knowledge</span><span style="color:var(--lavender)">generously.</span></div>

  <div class="vertical" style="left:30px;top:648px;font-size:50px;color:#4a92d8">Smile</div>
  <div class="vertical" style="left:92px;top:638px;font-size:20px;color:#8a5a1e;line-height:.95">and<br>have</div>
  <div class="line" style="left:92px;top:499px;font-size:23px">and infect others with</div>
  <div class="line" style="left:92px;top:540px;font-size:25px">your</div>
  <div class="line" style="left:165px;top:526px;font-size:42px;color:var(--sky)">happiness</div>
  <div class="line" style="left:153px;top:580px;font-size:54px;color:var(--orange)">fun<span style="font-size:20px;color:var(--red)">!</span></div>
  <div class="line" style="left:282px;top:569px;font-size:25px;letter-spacing:2px">firstly</div>
  <div class="line" style="left:282px;top:600px;font-size:25px;letter-spacing:4px">from</div>
  <div class="line" style="left:282px;top:630px;font-size:25px">within.</div>

  <div class="line" style="left:35px;top:656px;font-size:52px;color:#8a8a8a;font-weight:700">Seek <span style="color:var(--light-grey);font-weight:400">success</span></div>
  <div class="vertical" style="left:33px;top:828px;font-size:38px;color:var(--red)">Adopt</div>
  <div class="line" style="left:86px;top:722px;font-size:31px;color:var(--purple)">a <span style="color:var(--red)">'can do'</span> attitude</div>
  <div class="line" style="left:86px;top:760px;font-size:31px;color:var(--purple)">to everything that</div>
  <div class="line" style="left:86px;top:797px;font-size:31px;color:var(--purple)">comes your way.</div>

  <div class="line" style="left:395px;top:182px;font-size:68px;color:var(--red)">Respond</div>
  <div class="line" style="left:398px;top:254px;font-size:23px;color:var(--grey)">to complex situations</div>
  <div class="line" style="left:398px;top:280px;font-size:41px;color:var(--dark-red)">innovatively,</div>
  <div class="line" style="left:398px;top:318px;font-size:41px;color:var(--dark-red)">creatively <span style="font-size:22px;color:var(--grey);margin-left:55px">and</span></div>
  <div class="line" style="left:398px;top:362px;font-size:41px;color:var(--maroon)">safely <span style="font-size:24px;color:var(--grey);margin-left:8px">within the</span></div>
  <div class="line spread" style="left:398px;top:404px;width:262px;font-size:24px;color:var(--grey)"><span>scope</span><span>of</span><span>your</span></div>
  <div class="line spread" style="left:398px;top:435px;width:262px;font-size:24px;color:var(--grey)"><span>p</span><span>r</span><span>a</span><span>c</span><span>t</span><span>i</span><span>c</span><span>e</span><span>.</span></div>
  <div class="line" style="left:395px;top:470px;font-size:62px;color:var(--red);letter-spacing:1px">Support</div>
  <div class="line" style="left:396px;top:542px;font-size:31px;color:var(--cyan)">your colleagues</div>
  <div class="line spread" style="left:396px;top:579px;width:264px;font-size:31px;color:var(--cyan)"><span>and</span><span>champion</span></div>
  <div class="line spread" style="left:396px;top:616px;width:264px;font-size:31px;color:var(--cyan)"><span>their</span><span>purpose.</span></div>
  <div class="vertical" style="left:396px;top:830px;font-size:50px;color:var(--pink)">Always</div>
  <div class="line" style="left:463px;top:664px;font-size:29px;color:var(--pink)">be solution</div>
  <div class="line spread" style="left:463px;top:699px;width:195px;font-size:29px;color:var(--pink)"><span>f</span><span>o</span><span>c</span><span>u</span><span>s</span><span>e</span><span>d</span><span>.</span></div>
  <div class="line spread" style="left:463px;top:754px;width:392px;font-size:31px;color:var(--orange)"><span>do</span><span>the</span><span>right</span><span>thing</span></div>
  <div class="line spread" style="left:463px;top:793px;width:392px;font-size:31px;color:var(--orange)"><span>without</span><span>exception.</span></div>

  <div class="line" style="left:675px;top:184px;font-size:48px;color:var(--magenta)">Choose</div>
  <div class="line spread" style="left:675px;top:229px;width:180px;font-size:23px"><span>t</span><span>h</span><span>o</span><span>u</span><span>g</span><span>h</span><span>t</span><span>s</span></div>
  <div class="line spread" style="left:675px;top:256px;width:180px;font-size:23px"><span>wisely,</span><span>they</span></div>
  <div class="line spread" style="left:675px;top:283px;width:180px;font-size:23px"><span>create</span><span>your</span></div>
  <div class="line spread" style="left:675px;top:311px;width:180px;font-size:40px;color:var(--magenta)"><span>r</span><span>e</span><span>a</span><span>l</span><span>i</span><span>t</span><span>y</span><span style="font-size:24px">.</span></div>
  <div class="line" style="left:675px;top:364px;font-size:33px;color:var(--magenta)">Celebrate,</div>
  <div class="line" style="left:675px;top:399px;font-size:33px;color:var(--magenta)">respect <span style="font-size:24px;color:var(--purple)">and</span></div>
  <div class="line spread" style="left:675px;top:436px;width:180px;font-size:34px;color:var(--magenta)"><span>v</span><span>a</span><span>l</span><span>u</span><span>e</span></div>
  <div class="line" style="left:675px;top:475px;font-size:26px;color:var(--purple)">the diversity</div>
  <div class="line" style="left:675px;top:501px;font-size:26px;color:var(--purple)">of Australian</div>
  <div class="line spread" style="left:675px;top:528px;width:178px;font-size:24px;color:var(--purple)"><span>c</span><span>u</span><span>l</span><span>t</span><span>u</span><span>r</span><span>e</span><span>.</span></div>
  <div class="line" style="left:675px;top:562px;font-size:54px;color:var(--sky)">You</div>
  <div class="line" style="left:816px;top:590px;font-size:24px;color:var(--grey)">are</div>
  <div class="line" style="left:675px;top:617px;font-size:52px;color:var(--purple)">unique<span style="font-size:24px;color:var(--grey)">,</span></div>
  <div class="line spread" style="left:675px;top:678px;width:178px;font-size:25px;color:var(--grey)"><span>revel</span><span>in</span><span>your</span></div>
  <div class="line" style="left:675px;top:708px;font-size:27px;color:var(--sky)">individuality<span style="color:var(--grey)">.</span></div>

  <div class="line" style="left:35px;top:834px;font-size:48px;color:var(--sky)">Delight <span style="font-size:30px;color:var(--navy)">your</span> <span style="font-size:38px;color:var(--sky)">clients</span> <span style="font-size:30px;color:var(--navy)">and</span> <span style="font-size:38px;color:var(--navy)">colleagues</span></div>
  <div class="line" style="left:35px;top:886px;font-size:31px;color:#5a5a5a">by exceeding their expectations.</div>
  <div class="line" style="left:35px;top:918px;font-size:27px">Only <span style="font-size:38px;color:var(--purple)">follow</span> exceptional <span style="font-size:38px;color:var(--purple)">leaders</span>.</div>
  <div class="line" style="left:35px;top:964px;font-size:52px;color:var(--brown)">Always</div>
  <div class="line" style="left:229px;top:978px;font-size:32px;color:var(--pale-cyan);letter-spacing:1px">If there is no one left</div>
  <div class="line" style="left:35px;top:1022px;font-size:38px;color:var(--brown)">lead with</div>
  <div class="line" style="left:229px;top:1022px;font-size:32px;color:var(--pale-cyan);letter-spacing:1px">to follow, then</div>
  <div class="line" style="left:488px;top:1020px;font-size:54px;color:var(--sky)">lead<span style="font-size:26px;color:var(--orange)">!</span></div>
  <div class="line" style="left:35px;top:1062px;font-size:38px;color:var(--tan)">purpose, passion</div>
  <div class="line" style="left:292px;top:1096px;font-size:38px;color:var(--tan)"><span style="font-size:31px">and</span> commitment.</div>

  <div class="photo" role="img" aria-label="Photo of a smiling nurse in light blue scrubs holding a clipboard"></div>
  <div class="brand"><i></i><span>CalmPeak</span></div>
  <div class="foot-band">Live your <b>dream</b>.</div>
</main>
</body>
</html>
```